Coastline Premier Retreats Business Card Design

Design a business card for Coastline Premier Retreats. Look at the website for colors and reference. Card should have logo, name, title, office number, mobile number, email, URL and a tagline like, "Luxury Hotel & Resort Email Marketing" (This might change).

https://www.coastlinepremierretreats.example

The rest I will leave up to your imagination.

Contact Information for Business Card

Logo, name, title, office number, mobile number, email, URL and a tagline like, "Luxury Hotel & Resort Email Marketing" (This might change).

```html
<!DOCTYPE html>
<html lang="en">
<head>
<meta charset="utf-8">
<title>Coastline Premier Retreats – Business Card</title>
<link rel="stylesheet" href="https://fonts.googleapis.com/css2?family=Open+Sans:wght@400;700;800&display=swap">
<style>
  :root {
    --backdrop: #222223;
    --card-dark: #1e1e21;
    --brand-orange: #f47622;
    --orange-deep: #d8611a;
    --ink-light: #ffffff;
    --rule: #8a8a8e;
  }
  * { box-sizing: border-box; margin: 0; padding: 0; }
  html, body { width: 1200px; height: 780px; overflow: hidden; }
  body {
    background: var(--backdrop);
    font-family: "Open Sans", Arial, sans-serif;
    position: relative;
  }
  .card {
    position: absolute;
    top: 241px;
    width: 520px;
    height: 297px;
    overflow: hidden;
    box-shadow: 0 14px 30px rgba(0,0,0,.45);
  }
  .card--front { left: 60px; background: var(--card-dark); }
  .card--back  { left: 620px; background: var(--brand-orange); }

  /* front */
  .brand {
    position: absolute;
    left: 34px; top: 58px;
    display: flex; align-items: flex-start; gap: 10px;
  }
  .brand__mark {
    width: 14px; height: 14px; margin-top: 6px;
    background: var(--brand-orange);
  }
  .brand__name {
    width: 170px;
    color: var(--ink-light);
    font-weight: 800;
    font-size: 20px;
    line-height: 1.15;
    text-transform: uppercase;
    letter-spacing: .5px;
  }
  .tagline {
    position: absolute;
    left: 34px; bottom: 36px;
    color: var(--brand-orange);
    font-size: 12.5px;
  }
  .divider { position: absolute; left: 0; top: 0; }
  .person {
    position: absolute;
    left: 262px; top: 48px;
  }
  .person__name {
    font-weight: 800;
    font-size: 25px;
    line-height: 1.1;
    color: var(--ink-light);
  }
  .person__first { color: var(--brand-orange); }
  .person__title {
    color: var(--ink-light);
    font-size: 12px;
    margin-top: 3px;
  }
  .contacts {
    list-style: none;
    margin-top: 18px;
  }
  .contacts li {
    display: flex; align-items: center; gap: 7px;
    color: var(--ink-light);
    font-size: 10.5px;
    line-height: 1.75;
  }
  .contacts svg { width: 11px; height: 11px; flex: none; }

  /* back */
  .back-name {
    position: absolute;
    inset: 0;
    display: flex; align-items: center; justify-content: center;
    text-align: center;
    color: var(--orange-deep);
    font-weight: 800;
    font-size: 34px;
    line-height: 1.1;
    text-transform: uppercase;
    letter-spacing: 1px;
    padding: 0 60px;
  }
</style>
</head>
<body>

<section class="card card--front" aria-label="Card front">
  <div class="brand">
    <span class="brand__mark"></span>
    <span class="brand__name">Coastline Premier Retreats</span>
  </div>
  <p class="tagline">Luxury Hotel &amp; Resort Email Marketing</p>

  <svg class="divider" width="520" height="297" aria-hidden="true">
    <line x1="246" y1="42" x2="226" y2="226" stroke="var(--rule)" stroke-width="0.8"/>
  </svg>

  <div class="person">
    <h1 class="person__name"><span class="person__first">Marta</span> Novakova</h1>
    <p class="person__title">Co-Founder</p>
    <ul class="contacts">
      <li>
        <svg viewBox="0 0 12 12" aria-hidden="true"><path d="M2.5 1h2l1 2.6-1.3.9a6 6 0 0 0 3.3 3.3l.9-1.3 2.6 1v2A1.2 1.2 0 0 1 9.8 11 9 9 0 0 1 1 2.2 1.2 1.2 0 0 1 2.5 1z" fill="var(--brand-orange)"/></svg>
        (555) 014-2758
      </li>
      <li>
        <svg viewBox="0 0 12 12" aria-hidden="true"><rect x="3" y="0.8" width="6" height="10.4" rx="1" fill="none" stroke="var(--brand-orange)" stroke-width="1.2"/><circle cx="6" cy="9.2" r=".6" fill="var(--brand-orange)"/></svg>
        (555) 019-7777
      </li>
      <li>
        <svg viewBox="0 0 12 12" aria-hidden="true"><circle cx="6" cy="6" r="5" fill="none" stroke="var(--brand-orange)" stroke-width="1.1"/><ellipse cx="6" cy="6" rx="2.2" ry="5" fill="none" stroke="var(--brand-orange)" stroke-width="1"/><line x1="1" y1="6" x2="11" y2="6" stroke="var(--brand-orange)" stroke-width="1"/></svg>
        www.coastlinepremierretreats.example
      </li>
      <li>
        <svg viewBox="0 0 12 12" aria-hidden="true"><rect x="0.8" y="2.2" width="10.4" height="7.6" rx=".8" fill="none" stroke="var(--brand-orange)" stroke-width="1.1"/><path d="M1 2.6 6 6.6l5-4" fill="none" stroke="var(--brand-orange)" stroke-width="1.1"/></svg>
        info@coastlinepremierretreats.example
      </li>
    </ul>
  </div>
</section>

<section class="card card--back" aria-label="Card back">
  <p class="back-name">Coastline Premier Retreats</p>
</section>

</body>
</html>
```